A weight loss and fitness website design

I am into different types of modern weight loss techniques for people who are a little fatty and wish to be physically and mentally fit. Basically, the website is to teach people how to reduce weight using different methods such as diet, exercises, yoga and other forms. I would need an eye catching website which would make visitors want to come back. The will be also be different forms of exercises for a health and fit life. This said, my website is to have two categories of
1) weight loss techniques
2) exercise of fit and healthy living.
I prefer bright colors such as green, blue, yellow, and orange. Imagery should include before and after pictures of people suffering from obesity, people under going exercises.
Designers can get ideas and inspiration from the website fitlumen.com which i was previously part of the team.
Target Market(s)
My target audience are people suffering from obesity, malnutrition and physical deficiency.
Industry/Entity Type
Fitness
Coding
Coded - Design and coding required
Number of Pages Required
1 page
Look and feel

```html
<!DOCTYPE html>
<html lang="en">
<head>
<meta charset="utf-8">
<title>Verdant Fitness</title>
<link href="https://fonts.googleapis.com/css2?family=Montserrat:wght@400;600;700;800&family=Open+Sans:wght@400;600;700&display=swap" rel="stylesheet">
<style>
:root{
  --green:#8cbd1b;
  --green-dark:#76a312;
  --orange:#f26a21;
  --yellow:#f5b60e;
  --blue:#1aa6dd;
  --ink:#2b2b2b;
  --text:#777;
  --muted:#999;
  --light:#f1f1f1;
  --dark:#1b1b1b;
  --black:#050505;
  --white:#fff;
}
*{box-sizing:border-box;margin:0;padding:0}
html,body{width:1200px;height:4206px;overflow:hidden}
body{position:relative;background:var(--white);font-family:"Open Sans",Arial,sans-serif;color:var(--text);font-size:13px;line-height:1.6}
.abs{position:absolute}
h2,h3,h4{font-family:"Montserrat",Arial,sans-serif;color:var(--ink);text-transform:uppercase}

/* top bar + hero */
.topbar{left:0;top:0;width:1200px;height:36px;background:rgba(20,20,20,.92);z-index:3;color:#bbb;font-size:11px}
.topbar .call{left:100px;top:9px}
.topbar .call b{color:var(--green);font-weight:600}
.topbar .account{right:100px;top:9px;display:flex;gap:28px}
.topbar .account span::before{content:"";display:inline-block;width:7px;height:7px;border-radius:50%;background:var(--green);margin-right:6px}
.nav{left:101px;top:45px;width:998px;height:64px;background:var(--white);z-index:3;display:flex;align-items:center;justify-content:space-between;padding:0 24px}
.brand{font-family:"Montserrat",Arial,sans-serif;font-weight:800;font-size:25px;color:var(--green)}
.menu{display:flex;gap:30px;font-size:14px;color:#555}
.hero{left:0;top:0;width:1200px;height:603px;background:linear-gradient(180deg,#c0a47a 0%,#e7a45a 30%,#a1643a 58%,#3c2a1e 80%,#1c1612 100%)}
.hero-title{left:124px;top:272px;font-family:"Montserrat",Arial,sans-serif;font-weight:800;font-size:52px;line-height:1.3;color:var(--white);letter-spacing:2px;text-shadow:0 2px 6px rgba(0,0,0,.5)}
.arrow{top:324px;width:36px;height:36px;border-radius:50%;background:rgba(255,255,255,.25);display:flex;align-items:center;justify-content:center}

/* trainings */
.trainings-title{left:0;top:660px;width:1200px;text-align:center;font-size:27px;font-weight:700;line-height:1.5}
.tabs{left:168px;top:757px;width:861px;height:62px;display:flex}
.tab{flex:1;display:flex;align-items:center;justify-content:center;gap:10px;color:var(--white);font-family:"Montserrat",Arial,sans-serif;font-size:21px;text-transform:uppercase}
.tab.diet{background:var(--orange)}.tab.ex{background:var(--yellow)}.tab.yoga{background:var(--green)}.tab.aero{background:var(--blue)}
.panel{left:168px;top:819px;width:861px;height:232px;border:1px solid #e2e2e2;padding:26px 40px;box-shadow:0 3px 8px rgba(0,0,0,.06)}
.panel h3{font-size:17px;font-weight:600;margin-bottom:6px}
.panel p{font-size:12px;line-height:1.6}
.ticks{display:grid;grid-template-columns:repeat(3,1fr);gap:20px 0;margin-top:26px;font-size:13px;text-transform:uppercase;color:#666}
.ticks li{list-style:none;display:flex;gap:14px;align-items:center}

/* split sections */
.split{left:0;width:1200px;height:412px;background:var(--light)}
.photo{position:absolute;top:0;height:100%}
.split h3{font-size:19px;font-weight:600;margin-bottom:14px}
.split p{font-size:12px;line-height:1.7}
.bullets li{list-style:none;display:flex;gap:22px;align-items:flex-start;margin-top:14px;font-size:12px;line-height:1.6}
.more{display:inline-block;margin-top:18px;color:var(--green);font-size:12px;text-decoration:underline}

/* gyms */
.gyms h2{font-size:27px;font-weight:700}
.features{display:flex;gap:36px;margin-top:28px;text-align:center}
.feature{width:110px}
.feature .ico{width:62px;height:62px;border:2px solid #cfcfcf;border-radius:50%;margin:0 auto 12px;display:flex;align-items:center;justify-content:center}
.feature h4{font-size:13px;font-weight:700}
.feature p{font-size:11px;line-height:1.4}
.btn{display:inline-block;background:var(--green);color:var(--white);font-family:"Montserrat",Arial,sans-serif;font-weight:700;font-size:14px;text-transform:uppercase;padding:10px 18px}

/* testimonial */
.testimonial{left:0;top:2428px;width:1200px;height:348px;background:linear-gradient(160deg,#2c2c2c,#141414 55%,#262626)}
.testimonial h2{position:absolute;left:0;top:56px;width:1200px;text-align:center;color:var(--white);font-size:26px;font-weight:700}
.quote{position:absolute;top:130px;width:300px;text-align:center;color:#aaa;font-size:12px;line-height:1.7}
.quote .mark{font-family:Georgia,serif;font-size:64px;line-height:.8;color:var(--green);display:block;height:46px}
.quote .who{display:block;margin-top:12px;color:var(--yellow);font-size:14px}

/* training adjusts */
.adjust{left:0;top:2776px;width:1200px;height:463px;background:var(--light)}
.adjust h2{font-size:27px;font-weight:700;line-height:1.35;margin-bottom:18px}
.adjust p{font-size:12px;line-height:1.75;margin-bottom:14px}

/* team */
.team h2{text-align:center;font-size:27px;font-weight:700}
.team .intro{text-align:center;font-size:12px;line-height:1.6;width:520px;margin:12px auto 0}
.card{position:absolute;top:3426px;width:224px;height:247px;background:var(--white);box-shadow:0 2px 8px rgba(0,0,0,.15)}
.card .pic{height:172px}
.card .name{text-align:center;font-size:14px;color:var(--ink);padding-top:8px}
.card.active .name{background:var(--green);color:var(--white);height:75px;padding-top:18px}
.social{display:flex;gap:5px;justify-content:center;margin-top:4px}
.social i{width:16px;height:16px;border:1px solid #555;border-radius:50%}

/* contact */
.contact{left:0;top:3738px;width:1200px;height:468px;background:var(--black);color:#888}
.contact h2{position:absolute;top:66px;width:1200px;text-align:center;color:var(--white);font-size:26px;font-weight:700}
.contact .intro{position:absolute;left:270px;top:112px;width:660px;text-align:center;font-size:12px;line-height:1.6}
.field{position:absolute;top:173px;height:46px;border:1px solid #555;background:#111;color:#aaa;font-size:12px;padding:14px 16px}
.subscribe{position:absolute;left:477px;top:241px;width:246px;height:45px;background:var(--green);color:var(--white);text-align:center;line-height:45px;font-family:"Montserrat",Arial,sans-serif;font-weight:700;font-size:16px;text-transform:uppercase}
.info{position:absolute;top:312px;font-size:12px;line-height:1.6;display:flex;gap:14px;align-items:flex-start;color:#ccc}
.foot-social{position:absolute;left:905px;top:322px;display:flex;gap:14px}
.foot-social i{width:14px;height:14px;border-radius:50%;background:#777}
.copy{position:absolute;top:392px;width:1200px;text-align:center;font-size:11px;color:#777}
</style>
</head>
<body>

<div class="abs hero" role="img" aria-label="Photo of a couple jogging on a hillside road at sunset"></div>
<div class="abs topbar">
  <span class="abs call">Any Questions? Call Us: <b>150 - 320 - 774 - 18</b></span>
  <span class="abs account"><span>Member Login</span><span>Register</span></span>
</div>
<nav class="abs nav">
  <span class="brand">Verdant Fitness</span>
  <span class="menu"><span>Home</span><span>About</span><span>Features</span><span>Classes</span><span>Coaches</span><span>News</span><span>Blog</span><span>Gallery</span><span>Contact</span></span>
</nav>
<h1 class="abs hero-title">WELCOME TO<br>VERDANT FITNESS</h1>
<div class="abs arrow" style="left:30px"><svg width="12" height="14" viewBox="0 0 12 14"><path d="M9 1 3 7l6 6" fill="none" stroke="#fff" stroke-width="2"/></svg></div>
<div class="abs arrow" style="right:30px"><svg width="12" height="14" viewBox="0 0 12 14"><path d="M3 1l6 6-6 6" fill="none" stroke="#fff" stroke-width="2"/></svg></div>

<section>
  <h2 class="abs trainings-title">We offer a wide variety of trainings<br>to achieve the best results</h2>
  <div class="abs tabs">
    <div class="tab diet"><svg width="26" height="26" viewBox="0 0 26 26"><circle cx="13" cy="13" r="12" fill="#fff"/><path d="M13 19s-6-3.5-6-7.5a3 3 0 0 1 6-1 3 3 0 0 1 6 1c0 4-6 7.5-6 7.5z" fill="var(--orange)"/></svg>Diet</div>
    <div class="tab ex"><svg width="28" height="20" viewBox="0 0 28 20"><rect x="2" y="6" width="4" height="8" fill="#fff"/><rect x="22" y="6" width="4" height="8" fill="#fff"/><rect x="6" y="9" width="16" height="2" fill="#fff"/></svg>Exercises</div>
    <div class="tab yoga"><svg width="20" height="24" viewBox="0 0 20 24"><circle cx="10" cy="4" r="3" fill="#fff"/><path d="M2 10h16M10 8v8l-5 6M10 16l5 6" stroke="#fff" stroke-width="2" fill="none"/></svg>Yoga</div>
    <div class="tab aero"><svg width="22" height="24" viewBox="0 0 22 24"><circle cx="13" cy="4" r="3" fill="#fff"/><path d="M4 10l8-2 2 7 5 3M12 8l-3 9-5 5" stroke="#fff" stroke-width="2" fill="none"/></svg>Aerobics</div>
  </div>
  <div class="abs panel">
    <h3>How to reduce weight using diet</h3>
    <p>There are many variations of balanced eating plans available, but the majority of people find small, steady changes to daily meals easier to keep, by portion control, better snacks or fresh whole foods. If you are going to follow a plan, you need to be sure.</p>
    <ul class="ticks">
      <li><svg width="12" height="10" viewBox="0 0 12 10"><path d="M1 5l3.5 3.5L11 1" fill="none" stroke="var(--orange)" stroke-width="2"/></svg>Bonorum et malorum</li>
      <li><svg width="12" height="10" viewBox="0 0 12 10"><path d="M1 5l3.5 3.5L11 1" fill="none" stroke="var(--orange)" stroke-width="2"/></svg>Bonorum et malorum</li>
      <li><svg width="12" height="10" viewBox="0 0 12 10"><path d="M1 5l3.5 3.5L11 1" fill="none" stroke="var(--orange)" stroke-width="2"/></svg>Bonorum et malorum</li>
      <li><svg width="12" height="10" viewBox="0 0 12 10"><path d="M1 5l3.5 3.5L11 1" fill="none" stroke="var(--orange)" stroke-width="2"/></svg>Bonorum et malorum</li>
      <li><svg width="12" height="10" viewBox="0 0 12 10"><path d="M1 5l3.5 3.5L11 1" fill="none" stroke="var(--orange)" stroke-width="2"/></svg>Bonorum et malorum</li>
      <li><svg width="12" height="10" viewBox="0 0 12 10"><path d="M1 5l3.5 3.5L11 1" fill="none" stroke="var(--orange)" stroke-width="2"/></svg>Bonorum et malorum</li>
    </ul>
  </div>
</section>

<section class="abs split" style="top:1116px">
  <div class="photo" style="left:597px;width:603px;background:linear-gradient(135deg,#6fb4e3,#d9b08f 45%,#5b6f86 80%)" role="img" aria-label="Photo of a slim waist and a woman holding a dumbbell"></div>
  <div class="abs" style="left:100px;top:50px;width:420px">
    <h3>Weight loss techniques</h3>
    <p>There are many variations of proven weight loss methods available, but the majority need patience, habit and support to give results that last.</p>
    <ul class="bullets">
      <li><svg width="14" height="14" viewBox="0 0 14 14"><circle cx="7" cy="7" r="6" fill="none" stroke="var(--green)" stroke-width="2"/></svg>There are many ways to cut calories without feeling hungry.</li>
      <li><svg width="14" height="14" viewBox="0 0 14 14"><rect x="1" y="5" width="12" height="4" fill="var(--green)"/></svg>There are many ways to move more during a busy working day and keep going.</li>
      <li><svg width="14" height="14" viewBox="0 0 14 14"><path d="M7 1v12M1 7h12" stroke="var(--green)" stroke-width="2"/></svg>There are many ways to sleep better.</li>
      <li><svg width="14" height="14" viewBox="0 0 14 14"><path d="M2 7l3 3 7-7" fill="none" stroke="var(--green)" stroke-width="2"/></svg>There are many ways to track progress and stay motivated every single week.</li>
    </ul>
    <a class="more">Click Here To View More</a>
  </div>
</section>

<section class="abs split" style="top:1528px">
  <div class="photo" style="left:0;width:597px;background:linear-gradient(135deg,#e8e8e8,#9a9a9a 55%,#4a4a4a)" role="img" aria-label="Photo of a man and a woman training with dumbbells in a gym"></div>
  <div class="abs" style="left:665px;top:70px;width:435px">
    <h3>Exercise of fit and healthy living.</h3>
    <p>Regular movement keeps the heart strong and the mind clear. Short daily sessions of walking, stretching and strength work build a routine that lasts, while rest days let muscles recover. Start slow, listen to your body and add a little more each week until activity feels natural and easy to enjoy.</p>
    <p style="margin-top:14px">Mix cardio with light weights and mobility drills for balance. Drink water, eat well and track how you feel after each workout.</p>
    <a class="more">Click Here To View More</a>
  </div>
</section>

<section class="abs gyms" style="left:100px;top:2008px;width:560px">
  <h2>We are not like other fitness gyms</h2>
  <p style="margin-top:10px;font-size:13px;line-height:1.6">Our coaches build each plan around you, with friendly support, honest advice and classes for every level of fitness.</p>
  <div class="features">
    <div class="feature"><div class="ico"><svg width="26" height="26" viewBox="0 0 26 26"><rect x="3" y="5" width="20" height="18" rx="2" fill="none" stroke="#333" stroke-width="2"/><path d="M3 10h20M8 2v5M18 2v5" stroke="#333" stroke-width="2"/></svg></div><h4>Finibus bonorum</h4><p>Flexible class times to suit your week</p></div>
    <div class="feature"><div class="ico"><svg width="26" height="26" viewBox="0 0 26 26"><circle cx="15" cy="4" r="3" fill="#333"/><path d="M6 11l8-3 2 8 5 3M14 8l-3 9-5 6" stroke="#333" stroke-width="2" fill="none"/></svg></div><h4>Finibus bonorum</h4><p>Personal coaching from real experts</p></div>
    <div class="feature"><div class="ico"><svg width="28" height="26" viewBox="0 0 28 26"><circle cx="6" cy="19" r="5" fill="none" stroke="#333" stroke-width="2"/><circle cx="22" cy="19" r="5" fill="none" stroke="#333" stroke-width="2"/><path d="M6 19l6-8 5 8M12 11h6l4 8" stroke="#333" stroke-width="2" fill="none"/><circle cx="16" cy="4" r="2.5" fill="#333"/></svg></div><h4>Finibus bonorum</h4><p>Cardio plans that burn fat safely</p></div>
  </div>
  <a class="btn" style="margin-top:30px">Learn more</a>
</section>
<svg class="abs" style="left:658px;top:1996px" width="372" height="372" viewBox="0 0 372 372" role="img" aria-label="Circular collage of healthy food and people exercising">
  <circle cx="186" cy="186" r="184" fill="none" stroke="var(--green)" stroke-width="3"/>
  <path d="M186 186V8A178 178 0 0 0 8 186z" fill="#c96a3a"/>
  <path d="M186 186V8A178 178 0 0 1 364 186z" fill="#8a6a5a"/>
  <path d="M186 186H8A178 178 0 0 0 186 364z" fill="#b7b0a0"/>
  <path d="M186 186H364A178 178 0 0 1 186 364z" fill="#6a6a6a"/>
  <path d="M186 8v356M8 186h356" stroke="#fff" stroke-width="6"/>
  <circle cx="186" cy="186" r="52" fill="#fff" stroke="var(--green)" stroke-width="4"/>
  <text x="186" y="182" text-anchor="middle" font-family="Montserrat,Arial,sans-serif" font-weight="700" font-size="15" fill="var(--green)">Verdant</text>
  <text x="186" y="201" text-anchor="middle" font-family="Montserrat,Arial,sans-serif" font-weight="700" font-size="15" fill="var(--green)">Fitness</text>
</svg>

<section class="abs testimonial" role="img" aria-label="Dark photo of gym equipment behind the testimonials">
  <h2>Our client testimonial</h2>
  <div class="quote" style="left:102px"><span class="mark">&ldquo;</span>I must explain how this program changed the way I eat and train. The coaches gave me a clear plan, and every week I felt stronger and lighter than the week before.<span class="who">- Lena &amp; Mark Otis</span></div>
  <div class="quote" style="left:450px"><span class="mark">&ldquo;</span>I must explain how this program changed the way I eat and train. The coaches gave me a clear plan, and every week I felt stronger and lighter than the week before.<span class="who">- Lena &amp; Mark Otis</span></div>
  <div class="quote" style="left:798px"><span class="mark">&ldquo;</span>I must explain how this program changed the way I eat and train. The coaches gave me a clear plan, and every week I felt stronger and lighter than the week before.<span class="who">- Lena &amp; Mark Otis</span></div>
</section>

<section class="abs adjust">
  <div class="abs" style="left:101px;top:64px;width:342px;height:348px;background:#ddd;padding:8px">
    <div style="height:100%;background:linear-gradient(90deg,#e9e9e9 0 49.5%,#fff 49.5% 50.5%,#e9e9e9 50.5%)" role="img" aria-label="Before and after photos of a woman who lost weight"></div>
  </div>
  <div class="abs" style="left:519px;top:84px;width:580px">
    <h2>Your training adjusts based on your strengths &amp; weaknesses</h2>
    <p>Every body is different, so your plan changes as you grow. We test your strength, stamina and flexibility, then shape each session around what you need most. As you improve, the workouts become harder, and where you struggle we slow down and build a stronger base before moving on. Nobody is left behind, and nobody is held back.</p>
    <p>Regular check-ins show your progress in numbers you can see. We adjust meals, rest and training load so you keep moving forward, avoid injury and reach your goal weight in a healthy and steady way that lasts.</p>
  </div>
</section>

<section class="abs team" style="left:0;top:3239px;width:1200px">
  <h2 style="margin-top:8px">Meet our team</h2>
  <p class="intro">Our trained coaches bring years of experience in nutrition, strength and yoga, and they will guide you every step of your journey.</p>
</section>
<div class="card active" style="left:101px"><div class="pic" style="background:linear-gradient(#e6e6e6,#c9b79a)" role="img" aria-label="Photo of a fitness coach"></div><div class="name">Daniel Reyes</div></div>
<div class="card" style="left:359px"><div class="pic" style="background:linear-gradient(#6a5a4a,#d8b04a)" role="img" aria-label="Photo of a fitness coach"></div><div class="name">Daniel Reyes</div><div class="social"><i></i><i></i><i></i></div></div>
<div class="card" style="left:618px"><div class="pic" style="background:linear-gradient(#cfc4b8,#8a6a5a)" role="img" aria-label="Photo of a yoga coach"></div><div class="name">Daniel Reyes</div><div class="social"><i></i><i></i><i></i></div></div>
<div class="card" style="left:876px"><div class="pic" style="background:linear-gradient(#f2f2f2,#d9b49a)" role="img" aria-label="Photo of a fitness coach"></div><div class="name">Daniel Reyes</div><div class="social"><i></i><i></i><i></i></div></div>

<footer class="abs contact">
  <h2>Contact us</h2>
  <p class="intro">Have a question about our plans or classes? Send us a message and our team will get back to you with friendly advice within one working day.</p>
  <div class="field" style="left:135px;width:300px">Enter Your Name</div>
  <div class="field" style="left:449px;width:302px">Enter Your Mail id</div>
  <div class="field" style="left:760px;width:303px">Enter Your Phone Number</div>
  <div class="subscribe">Subscribe now</div>
  <div class="info" style="left:126px"><svg width="12" height="16" viewBox="0 0 12 16"><path d="M6 15S1 9 1 6a5 5 0 0 1 10 0c0 3-5 9-5 9z" fill="var(--yellow)"/><circle cx="6" cy="6" r="2" fill="#000"/></svg><span>12 Linden Park Road, 40210<br>Oakfield, Greenvale</span></div>
  <div class="info" style="left:440px"><svg width="14" height="14" viewBox="0 0 14 14"><path d="M3 1l3 3-2 2a8 8 0 0 0 4 4l2-2 3 3-2 2C6 13 1 8 1 3z" fill="var(--yellow)"/></svg><span>Mobile Number : +4405218873<br>Toll free : +1800 644271930</span></div>
  <div class="info" style="left:686px;top:320px"><svg width="16" height="12" viewBox="0 0 16 12"><rect x="1" y="1" width="14" height="10" fill="none" stroke="var(--yellow)" stroke-width="1.5"/><path d="M1 1l7 6 7-6" fill="none" stroke="var(--yellow)" stroke-width="1.5"/></svg><span>hello@verdantfit.com</span></div>
  <div class="foot-social"><i></i><i></i><i></i><i></i><i></i></div>
  <p class="copy">Copyright &copy; 2016 Verdant Fitness . All rights reserved.</p>
</footer>

</body>
</html>
```